one pager for investors

I will give an initial file in any format needed. Also, the photo that must be included. As well as the logo, that must be the key to the overall design in terms of font, colors, and general layout. I will attach a file in PDF format, which is a one pager presenting a project for investors that I would like to attract and convinced to invest in my project. What I would like you to do is propose me different and better design options, taking my first draft as an example. But you must absolutely keep every single word and number, absolutely all the information written in my first draft(except “ TEMPLATE DRAFT”). Also, on the top left corner is the logo of our company, which I think should be your main inspiration document is a one pager presented to potential investors that not only has to include the most important information in order for them to be able to see everything needed to see the value of the project (which I’ve already taken care of by writing the text needed, numbers presented and timeline shown; all of which which must be preserved in terms of content, but can be completely redesigned and manipulated ) sh a.k.a. Project summary for investor to go for it.
Serious rich investors
Real eatate

```html
<!DOCTYPE html>
<html lang="fr">
<head>
<meta charset="utf-8">
<title>Projet immobilier XXX – résumé investisseurs</title>
<link rel="stylesheet" href="https://fonts.googleapis.com/css2?family=Poppins:wght@300;400;600;700&family=Anton&display=swap">
<style>
  :root {
    --backdrop: #d8cfca;
    --brand-blue: #3f5aa9;
    --brand-navy: #1c2130;
    --panel-grey: #a7a9ac;
    --alert-red: #e8202a;
    --alert-yellow: #f7e600;
    --footer-grey: #7b7d80;
    --white: #ffffff;
  }
  * { margin: 0; padding: 0; box-sizing: border-box; }
  html, body {
    width: 1200px; height: 853px; overflow: hidden;
    background: var(--backdrop);
    font-family: "Poppins", sans-serif;
  }
  .sheet {
    position: absolute; left: 298px; top: 0;
    width: 603px; height: 853px;
    background: var(--white);
    overflow: hidden;
  }
  .sheet-shapes { position: absolute; inset: 0; }
  .hero-photo {
    position: absolute; left: 0; top: 0; width: 603px; height: 300px;
    background: linear-gradient(180deg, #d9dde6 0%, #b9a99a 45%, #7d6a5a 70%, #c9c5c0 88%, #ffffff 100%);
  }
  .brand-pill {
    position: absolute; left: 0; top: 18px; width: 352px; height: 113px;
    background: var(--white);
    border-radius: 0 57px 57px 0;
  }
  .brand-name {
    position: absolute; left: 22px; top: 56px;
    color: var(--brand-navy); font-weight: 700;
    font-size: 30px; line-height: 1; white-space: nowrap;
  }

  .badge {
    position: absolute; left: 404px; top: 211px; width: 192px; height: 192px;
    border-radius: 50%; background: var(--alert-red);
    color: var(--alert-yellow); text-align: center;
  }
  .badge-title { font-family: "Anton", sans-serif; font-size: 31px; line-height: 1; margin-top: 50px; }
  .badge-sub { font-size: 18px; line-height: 1.2; margin-top: 6px; }

  .description { position: absolute; left: 20px; top: 314px; width: 420px; color: var(--white); }
  .description h2 { font-size: 24px; font-weight: 700; line-height: 1.1; margin-bottom: 12px; }
  .description p { font-size: 13.4px; font-weight: 400; line-height: 15.7px; }

  .duration {
    position: absolute; left: 17px; top: 471px;
    font-size: 22.5px; font-weight: 700; color: var(--brand-navy); line-height: 1.1; white-space: nowrap;
  }
  .finance-row {
    position: absolute; font-size: 12.2px; line-height: 1; color: var(--white); font-weight: 400; white-space: nowrap;
  }
  .finance-row.strong { font-weight: 700; }
  .col-a { left: 19px; } .col-b { left: 176px; } .col-c { left: 311px; } .col-d { left: 501px; }

  .timeline-text { position: absolute; color: var(--white); font-size: 12.2px; line-height: 1; white-space: nowrap; }
  .timeline-date { font-weight: 700; }

  .footer-alert {
    position: absolute; left: 0; width: 603px; top: 802px; text-align: center;
    color: var(--alert-red); font-weight: 600; font-size: 14px; line-height: 1;
  }
  .footer-address {
    position: absolute; left: 0; width: 603px; top: 822px; text-align: center;
    color: var(--footer-grey); font-size: 14px; line-height: 1; font-weight: 400;
  }
  .footer-address strong { font-weight: 700; }
</style>
</head>
<body>
<main class="sheet">
  <div class="hero-photo" role="img" aria-label="Rendu architectural d'un immeuble résidentiel moderne à terrasses, entouré de jardins"></div>

  <svg class="sheet-shapes" width="603" height="853" viewBox="0 0 603 853" aria-hidden="true">
    <polygon points="0,284 425,284 493,462 0,462" fill="var(--brand-blue)"/>
    <rect x="0" y="462" width="603" height="235" fill="var(--panel-grey)"/>
    <polygon points="0,697 582,697 603,761 603,800 0,800" fill="var(--brand-blue)"/>
    <g stroke="var(--white)" stroke-width="3">
      <line x1="24" y1="743" x2="552" y2="743"/>
      <line x1="53" y1="728" x2="53" y2="761"/>
      <line x1="151" y1="728" x2="151" y2="761"/>
      <line x1="294" y1="728" x2="294" y2="761"/>
      <line x1="489" y1="728" x2="489" y2="761"/>
    </g>
    <polygon points="549,736 563,743 549,750" fill="var(--white)"/>
  </svg>

  <div class="brand-pill"></div>
  <div class="brand-name">Verano Properties SA</div>

  <section class="description">
    <h2>Description du projet</h2>
    <p>Le projet XXX est un projet de dévloppement de 30 appartements de standing en PPE au centre de Lausanne. Le terrain a été sécurisé par la signature du vente à terme conditionnelle. L’objectif est d’obtenir le permis de construire, puis de ventre les lots. Dans un premier temps sur plan puis au fil de la construction.</p>
  </section>

  <div class="badge">
    <div class="badge-title">CONFIDENTIEL</div>
    <div class="badge-sub">– Projet imobilier<br>“XXX”</div>
  </div>

  <h2 class="duration">Durée estimée du projet – 24 à 36 mois.</h2>

  <div class="finance-row strong col-a" style="top:502px">Plan financier</div>
  <div class="finance-row col-a" style="top:531px">Prix du terrain</div>
  <div class="finance-row col-b" style="top:531px">CHF 2’000’000</div>
  <div class="finance-row col-a" style="top:545px">Frais d’acquisition</div>
  <div class="finance-row col-b" style="top:545px">CHF 100’000</div>
  <div class="finance-row col-a" style="top:560px">Coût de construction</div>
  <div class="finance-row col-b" style="top:560px">CHF 2’500’000</div>
  <div class="finance-row col-a" style="top:574px">Divers &amp; imprévus</div>
  <div class="finance-row col-b" style="top:574px">CHF 200’000</div>
  <div class="finance-row strong col-a" style="top:589px">Prix de revient total</div>
  <div class="finance-row strong col-b" style="top:589px">CHF 4’800’000</div>
  <div class="finance-row strong col-a" style="top:618px">Prix de vente total</div>
  <div class="finance-row strong col-b" style="top:618px">CHF 7’500’000</div>
  <div class="finance-row col-a" style="top:633px">Honoraires sur vente</div>
  <div class="finance-row col-b" style="top:633px">CHF 190’000</div>
  <div class="finance-row strong col-a" style="top:662px">Marge projet</div>
  <div class="finance-row strong col-b" style="top:662px">CHF 2’510’000</div>
  <div class="finance-row col-a" style="top:677px">En % sur prix de vente</div>
  <div class="finance-row col-b" style="top:677px">33.47%</div>

  <div class="finance-row strong col-c" style="top:515px">Structure d’investissement</div>
  <div class="finance-row col-c" style="top:545px">Besoin de fonds propres</div>
  <div class="finance-row col-d" style="top:545px">CHF 2’000’000</div>
  <div class="finance-row col-c" style="top:559px">Retour de fonds total</div>
  <div class="finance-row col-d" style="top:559px">CHF 3’156’600</div>
  <div class="finance-row strong col-c" style="top:588px">Bénéfice net investisseur</div>
  <div class="finance-row strong col-d" style="top:588px">CHF 1’656’600</div>
  <div class="finance-row col-c" style="top:603px">Soit 2/3 du bénéfice projet</div>
  <div class="finance-row strong col-c" style="top:632px">Multiple sur fonds propres</div>
  <div class="finance-row strong col-d" style="top:632px">x1.83</div>
  <div class="finance-row strong col-c" style="top:662px">Rendement annualisé</div>
  <div class="finance-row strong col-d" style="top:662px">41.4%</div>
  <div class="finance-row col-c" style="top:677px">Calcul sur 24 mois</div>

  <div class="timeline-text timeline-date" style="left:33px;top:710px">08.2024</div>
  <div class="timeline-text timeline-date" style="left:126px;top:710px">04.2025</div>
  <div class="timeline-text timeline-date" style="left:270px;top:710px">12.2025</div>
  <div class="timeline-text timeline-date" style="left:463px;top:710px">12.2025</div>
  <div class="timeline-text" style="left:18px;top:773px">Achat parcelle</div>
  <div class="timeline-text" style="left:115px;top:773px">Mise à l’enquête</div>
  <div class="timeline-text" style="left:245px;top:771px">Début construction</div>
  <div class="timeline-text" style="left:466px;top:773px">Livraison</div>

  <div class="footer-alert">CONFIDENTIEL</div>
  <div class="footer-address"><strong>Verano Properties Vaud SA</strong> - Rue des Vergers 12 - CH-1260 Nyon</div>
</main>
</body>
</html>
```